Professional & attention grabbing.

A business card design, front and back. I already have a logo I will attach, but I am open to something new as well.
Things to include:
Name:
Title:
Phone:
Email:
Wanting something that is professional but attention grabbing.
Also we do a lot of work using drones on natural gas pipelines (leading the future)if you want to include any of that. I'm open to ideas.
Target Market(s)
Natural gas transmission industry / greenhouse gas mitigation industry
Industry/Entity Type
Business
Colors
Designer to choose colors to be used in the design.
Look and feel
Each slider illustrates characteristics of the customer's brand and the style your logo design should communicate.

```html
<!DOCTYPE html>
<html lang="en">
<head>
<meta charset="utf-8">
<title>Keelwater Inspections – Business Card</title>
<link rel="stylesheet" href="https://fonts.googleapis.com/css2?family=Open+Sans:wght@400;600;700&family=Saira:wght@700&display=swap">
<style>
  :root {
    --bg: #4a4a4c;
    --card-dark: #232326;
    --card-dark-2: #35353a;
    --card-light: #ffffff;
    --red: #d9201f;
    --red-dark: #b3171a;
    --ink: #2c2c2f;
    --grey: #6b6b70;
    --rule: #8a8a8f;
    --white: #ffffff;
  }
  * { box-sizing: border-box; margin: 0; padding: 0; }
  html, body {
    width: 1200px; height: 852px; overflow: hidden;
    background: var(--bg);
    font-family: "Open Sans", Arial, sans-serif;
  }
  .stage { position: relative; width: 1200px; height: 852px; }

  .card {
    position: absolute; width: 540px; height: 310px;
    border-radius: 18px; overflow: hidden;
    box-shadow: 0 14px 30px rgba(0,0,0,.35);
  }

  /* Front */
  .card--front {
    left: 70px; top: 110px;
    background: linear-gradient(135deg, var(--card-dark-2), var(--card-dark) 60%);
  }
  .brand {
    display: flex; align-items: center; gap: 10px;
    font-weight: 700; letter-spacing: .5px; text-transform: uppercase;
  }
  .brand__mark { width: 22px; height: 22px; background: var(--red); }
  .card--front .brand {
    position: absolute; left: 110px; top: 108px;
    color: var(--white); font-size: 27px;
  }
  .front-band {
    position: absolute; left: 0; right: 0; top: 232px; height: 40px;
    background: var(--red);
    display: flex; align-items: center; padding-left: 40px;
    color: var(--white); font-size: 15px; font-weight: 600;
  }

  /* Back */
  .card--back {
    left: 590px; top: 440px;
    background: var(--card-light);
  }
  .card--back .brand {
    position: absolute; right: 36px; top: 40px;
    color: var(--ink); font-size: 22px;
  }
  .brand-rule {
    position: absolute; left: 250px; right: 36px; top: 86px;
    height: 1px; background: var(--rule);
  }
  .address {
    position: absolute; right: 36px; top: 104px;
    text-align: right; font-size: 13px; line-height: 1.45; color: var(--ink);
  }
  .tagline-tab {
    position: absolute; right: 0; top: 160px; width: 240px; height: 38px;
    background: var(--red);
    border-top-left-radius: 4px;
    display: flex; align-items: center; justify-content: center;
    color: var(--white); font-size: 14px; font-weight: 600;
  }
  .base-strip {
    position: absolute; left: 0; right: 0; bottom: 0; height: 18px;
    background: var(--card-dark);
  }
  .person { position: absolute; left: 32px; top: 178px; }
  .person__name {
    font-family: "Saira", "Arial Black", sans-serif;
    font-size: 22px; color: var(--red); letter-spacing: 1px; line-height: 1;
  }
  .person__title { font-size: 12.5px; color: var(--ink); margin-top: 4px; }
  .name-rule {
    position: absolute; left: 220px; right: 250px; top: 200px;
    height: 1px; background: var(--rule);
  }
  .contacts {
    position: absolute; left: 32px; top: 226px;
    list-style: none; font-size: 13.5px; color: var(--ink);
  }
  .contacts li { display: flex; align-items: center; gap: 9px; line-height: 19px; }
  .contacts svg { width: 12px; height: 12px; fill: var(--red); flex: none; }
</style>
</head>
<body>
<main class="stage">

  <section class="card card--front" aria-label="Card front">
    <div class="brand"><span class="brand__mark"></span>Keelwater Inspections</div>
    <div class="front-band">Also we do a lot of work using drones on natural gas pipelines</div>
  </section>

  <section class="card card--back" aria-label="Card back">
    <div class="brand"><span class="brand__mark"></span>Keelwater Inspections</div>
    <div class="brand-rule"></div>
    <p class="address">88 Harbour Lane,<br>Eastport NSW 2100</p>
    <div class="tagline-tab">Drones on natural gas pipelines</div>

    <div class="person">
      <h1 class="person__name">DANIEL HART</h1>
      <p class="person__title">Managing Director</p>
    </div>
    <div class="name-rule"></div>

    <ul class="contacts">
      <li><svg viewBox="0 0 12 12" aria-hidden="true"><path d="M1 4c0-2 2-3 5-3s5 1 5 3v1H8V4H4v1H1zM3 6h6l2 5H1z"/></svg>1300 555 014</li>
      <li><svg viewBox="0 0 12 12" aria-hidden="true"><circle cx="6" cy="6" r="5.5"/><path d="M.5 6h11M6 .5v11" stroke="#fff" stroke-width="1"/></svg>www.keelwater-demo.com</li>
      <li><svg viewBox="0 0 12 12" aria-hidden="true"><path d="M0 2h12v8H0z"/><path d="M0 2l6 5 6-5" stroke="#fff" stroke-width="1" fill="none"/></svg>daniel.hart@keelwater-demo.com</li>
    </ul>
    <div class="base-strip"></div>
  </section>

</main>
</body>
</html>
```